Hearthline Insurance Provider Website

We are selling Hearthline Insurance policy / tenants Policy/Flood Insurance in USA in few states and planning expand nationally.

Our target audience are two folds: Customers (Buy policies) and Insurance Agents who wants to work with us to sell our policies to customers. But website should focus 80% on customers and 20% on agents. So, more customer focused user experience. Please note that there is no direct buy option for customers. They always go through insurance agents.

Customer focused, educational that makes buyer journey easy. We don’t want to come off as trying sell something as there is no direct sales involved from website.

Target Market(s)

Homeowners in USA and Insurance agent who sells these insurance.

Industry/Entity Type

Insurance

Number of Pages Required

4 page

Font styles to use
Other font styles liked:
• Open to suggestions

Colors

Designer to choose colors to be used in the design.

Requirements
Must have
• Three most important things: Trustworthy, Authentic, Simple
• Please use colors form logo and grays
• We like: www.hollowmere.com
• https://www.quillfenbrook.com/
• We need Agent Look up tool on home page similar to what is shown on example sites.
• Design:
• Home Page - Open to Ideas
• Insurance (Products) Landing Page - Info similar to: https://www.quillfenbrook.com/insurance/
• Agents Page - https://www.quillfenbrook.com/agents/
• Claims Page - Information similar to: https://www.quillfenbrook.com/claims-center/
• Site Navigation:
• Home
• Insurance
• Claims
• Agents
• About Us
• Contact Us
Nice to have
• Elegant, minimal and clean design that reflects trust and authenticity.
Should not have
• Slider or rotating images - prefer flat design. Not over powering design.

```html
<!DOCTYPE html>
<html lang="en">
<head>
<meta charset="utf-8">
<title>Hearthline Insurance Co. — Home</title>
<link href="https://fonts.googleapis.com/css2?family=Montserrat:wght@600;700&family=Source+Sans+3:wght@400;600&display=swap" rel="stylesheet">
<style>
:root{
  --navy:#1f3a78;
  --navy-deep:#1c3670;
  --red:#d92b35;
  --ink:#1a1a1a;
  --gray-text:#4a4a4a;
  --gray-line:#cfcfcf;
  --white:#ffffff;
}
*{box-sizing:border-box;margin:0;padding:0}
html,body{width:1183px;height:1200px;overflow:hidden}
body{position:relative;background:var(--white);font-family:"Source Sans 3",sans-serif;color:var(--gray-text)}
a{color:inherit;text-decoration:none}

.site-header{position:absolute;left:0;top:0;width:1183px;height:74px;background:var(--white)}
.brand{position:absolute;left:170px;top:22px;display:flex;align-items:center;gap:8px}
.brand-mark{width:30px;height:30px;border-radius:50%;background:var(--navy)}
.brand-name{font-family:"Source Sans 3",sans-serif;font-weight:600;font-size:17px;color:var(--navy);line-height:1.05;width:150px}
.main-nav{position:absolute;left:437px;top:28px;display:flex;gap:18px;font-size:13px;font-weight:600;color:#555}
.main-nav .is-active{color:var(--red)}
.header-btn{position:absolute;top:20px;height:32px;border-radius:2px;color:var(--white);font-size:13px;font-weight:600;display:flex;align-items:center;justify-content:center;gap:5px}
.btn-careers{left:838px;width:85px;background:var(--navy)}
.btn-login{left:927px;width:86px;background:var(--red)}

.hero{position:absolute;left:0;top:74px;width:1183px;height:443px}
.hero-photo{position:absolute;inset:0;background:linear-gradient(90deg,#cfc9c4 0%,#e6e2de 30%,#f3f2f1 55%,#f5f5f5 100%)}
.hero-content{position:absolute;left:560px;top:90px;width:424px;text-align:center}
.hero-emblem{width:46px;height:46px;border-radius:50%;background:var(--navy);margin:0 auto 16px}
.hero-title{font-family:"Montserrat",sans-serif;font-weight:700;font-size:26px;color:var(--ink);letter-spacing:-.3px}
.hero-text{margin-top:26px;font-size:14.5px;line-height:22px;font-weight:600;color:#555}
.agent-search{position:absolute;left:66px;top:253px;display:flex;gap:8px}
.zip-field{width:145px;height:40px;border:1px solid var(--gray-line);background:var(--white);font-size:12px;color:#999;padding:0 13px;display:flex;align-items:center}
.btn-find{width:139px;height:40px;background:var(--navy);color:var(--white);font-size:14px;font-weight:600;display:flex;align-items:center;justify-content:center;gap:7px;border-radius:2px}

.products{position:absolute;left:0;top:556px;width:1183px;text-align:center}
.products-title{font-family:"Montserrat",sans-serif;font-weight:700;font-size:26px;color:var(--ink);letter-spacing:-.3px}
.products-sub{margin-top:5px;font-size:13.5px;font-weight:600;color:#666}
.product-grid{position:absolute;top:92px;left:170px;display:flex;gap:5px}
.product-card{width:207px}
.product-photo{height:192px}
.product-name{margin-top:14px;font-size:14px;font-weight:600;color:#333}

.site-footer{position:absolute;left:0;top:912px;width:1183px;height:288px;background:var(--navy);color:var(--white)}
.footer-col{position:absolute;top:41px}
.footer-col h3{font-size:14px;font-weight:600;margin-bottom:14px}
.footer-col li{list-style:none;font-size:11.5px;line-height:19.2px}
.contact-phone{font-size:15.5px;font-weight:600;line-height:18px}
.contact-mail{font-size:11.5px}
.social{display:flex;gap:5px;margin-top:15px}
.social span{width:30px;height:30px;border:1.5px solid var(--white);border-radius:50%}
.btn-outline{margin-top:21px;width:139px;height:40px;border:1.5px solid var(--white);border-radius:2px;display:flex;align-items:center;justify-content:center;gap:7px;font-size:14px;font-weight:600}
.footer-legal{position:absolute;top:208px;width:100%;text-align:center;font-size:11.5px;line-height:19.5px}
</style>
</head>
<body>
<header class="site-header">
  <a class="brand" href="#"><span class="brand-mark"></span><span class="brand-name">Hearthline Insurance Co.</span></a>
  <nav class="main-nav">
    <a class="is-active" href="#">Home</a><a href="#">Insurance</a><a href="#">About Us</a><a href="#">Claims</a><a href="#">Agents</a><a href="#">Contact Us</a>
  </nav>
  <a class="header-btn btn-careers" href="#">
    <svg width="11" height="12" viewBox="0 0 11 12"><circle cx="5.5" cy="3.2" r="2.7" fill="#fff"/><path d="M0.5 12c0-3.4 2.2-5 5-5s5 1.6 5 5z" fill="#fff"/></svg>Careers</a>
  <a class="header-btn btn-login" href="#">
    <svg width="10" height="12" viewBox="0 0 10 12"><path d="M2.5 5V3.5a2.5 2.5 0 015 0V5" stroke="#fff" stroke-width="1.6" fill="none"/><rect x="1" y="5" width="8" height="7" rx="1" fill="#fff"/></svg>Login</a>
</header>

<section class="hero">
  <div class="hero-photo" role="img" aria-label="Smiling woman relaxing on a sofa with a coffee cup and laptop in a bright living room"></div>
  <div class="hero-content">
    <div class="hero-emblem"></div>
    <h1 class="hero-title">Find an Agent</h1>
    <p class="hero-text">Talk to one of our local independent agencies to get a quote,<br>ask questions about coverage options &amp; more!</p>
    <div class="agent-search">
      <div class="zip-field">ZIP Code</div>
      <a class="btn-find" href="#">
        <svg width="18" height="18" viewBox="0 0 18 18" fill="none" stroke="#fff" stroke-width="1.5"><circle cx="8" cy="8" r="6.5"/><circle cx="8" cy="6.5" r="2"/><path d="M4.5 11.5c1-1.6 2.2-2.2 3.5-2.2s2.5.6 3.5 2.2M12.8 12.8l4 4"/></svg>Find an Agent</a>
    </div>
  </div>
</section>

<section class="products">
  <h2 class="products-title">Get insurance for almost anything you need</h2>
  <p class="products-sub">Protection through one of the best insurance companies</p>
  <div class="product-grid">
    <div class="product-card"><div class="product-photo" role="img" aria-label="Couple standing at the front door of their home" style="background:linear-gradient(160deg,#9a9a92,#5b4a3c 60%,#7a2a25)"></div><p class="product-name">Homeowners</p></div>
    <div class="product-card"><div class="product-photo" role="img" aria-label="Tall modern apartment building under a blue sky" style="background:linear-gradient(180deg,#a9c6e2,#6d7178 55%,#4d5a3c)"></div><p class="product-name">Renters/Condo</p></div>
    <div class="product-card"><div class="product-photo" role="img" aria-label="House roof burning with flames and smoke" style="background:linear-gradient(180deg,#9ea39c,#c55a2a 60%,#5a3328)"></div><p class="product-name">Dwelling Fire</p></div>
    <div class="product-card"><div class="product-photo" role="img" aria-label="Insurance agent holding a folder outside a brick house" style="background:linear-gradient(160deg,#8a5a45,#a8a49a 50%,#4f7a3a)"></div><p class="product-name">Agent Locator Tool</p></div>
  </div>
</section>

<footer class="site-footer">
  <div class="footer-col" style="left:170px">
    <h3>Contact Info</h3>
    <p class="contact-phone">1800 555 0142</p>
    <p class="contact-mail">info@hearthlineinsurance.co</p>
    <div class="social"><span></span><span></span><span></span><span></span></div>
  </div>
  <div class="footer-col" style="left:386px">
    <h3>Our Company</h3>
    <ul><li>Home</li><li>Insurance</li><li>About Us</li><li>Claims</li><li>Agents</li></ul>
  </div>
  <div class="footer-col" style="left:530px">
    <h3>Login to Your Account</h3>
    <ul><li>Agents Login</li><li>Clients login</li></ul>
    <a class="btn-outline" href="#">
      <svg width="18" height="18" viewBox="0 0 18 18" fill="none" stroke="#fff" stroke-width="1.5"><circle cx="8" cy="8" r="6.5"/><circle cx="8" cy="6.5" r="2"/><path d="M4.5 11.5c1-1.6 2.2-2.2 3.5-2.2s2.5.6 3.5 2.2M12.8 12.8l4 4"/></svg>Find an Agent</a>
  </div>
  <div class="footer-col" style="left:724px">
    <h3>Customer Support</h3>
    <ul><li>FAQs</li><li>Resources</li><li>Report a Claim</li><li>Find an Agent</li></ul>
  </div>
  <div class="footer-col" style="left:890px">
    <h3>Connect With Us</h3>
    <ul><li>Support</li><li>Careers</li></ul>
  </div>
  <div class="footer-legal">
    <p>Copyright ©2018 Hearthline Insurance. All Rights Reserved</p>
    <p>Terms of Use &nbsp;-&nbsp; Privacy Policy &nbsp;-&nbsp; Sitemap</p>
  </div>
</footer>
</body>
</html>
```